Business card por a urban DJ, up scale audience target

Need a sober design, modern, conservative colors but i can consider some options, y play rnb, hip hop, EDM and top40.

Business card for contact and personal info, double sided, use logo attrached please; im 42 so i need a card acording to my age an target audience.

Target Market(s)

Adult people, up scale audience

Industry/Entity Type

Music Download

Contact Information for Business Card

Cel (318) 4207265518 www.lumadrift.com

Requirements
Must have
• open mind
Nice to have
• open mind
Should not have
• DJ

```html
<!DOCTYPE html>
<html lang="en">
<head>
<meta charset="utf-8">
<title>Luma Business Card</title>
<link href="https://fonts.googleapis.com/css2?family=Open+Sans:wght@400;600;700;800&display=swap" rel="stylesheet">
<style>
  :root {
    --page: #e9e7e3;
    --ink: #2b2b2b;
    --ink-deep: #232323;
    --paper: #f4f4f4;
    --silver: #bdbdbd;
    --silver-light: #d6d6d6;
    --text-light: #f2f2f2;
    --text-muted: #cfcfcf;
  }
  * { margin: 0; padding: 0; box-sizing: border-box; }
  html, body {
    width: 1200px; height: 780px; overflow: hidden;
    background: var(--page);
    font-family: "Open Sans", Arial, sans-serif;
  }
  .canvas {
    position: relative; width: 1200px; height: 780px;
    display: flex; align-items: center; justify-content: center; gap: 50px;
  }
  .card {
    position: relative; width: 540px; height: 310px;
    border-radius: 4px; overflow: hidden;
    box-shadow: 0 10px 28px rgba(0,0,0,0.22), 0 2px 5px rgba(0,0,0,0.18);
  }
  .card-front { background: var(--paper); }
  .card-back { background: var(--ink); }
  .card-shape { position: absolute; inset: 0; width: 100%; height: 100%; }

  .brand-name {
    position: absolute;
    font-family: "Open Sans", Arial, sans-serif;
    font-weight: 800; letter-spacing: 4px; line-height: 1;
  }
  .card-front .brand-name {
    left: 40px; top: 118px; font-size: 66px; color: var(--ink-deep);
  }
  .card-back .brand-name {
    left: 210px; top: 118px; font-size: 72px; color: var(--text-light);
  }

  .identity { position: absolute; left: 330px; top: 46px; color: var(--text-light); }
  .identity-name { font-size: 19px; font-weight: 700; letter-spacing: 0.5px; }
  .identity-role { font-size: 13px; font-weight: 400; color: var(--text-muted); margin-top: 2px; }

  .contact-list { position: absolute; left: 330px; top: 196px; list-style: none; }
  .contact-item {
    display: flex; align-items: center; gap: 8px;
    font-size: 13px; color: var(--text-light); line-height: 21px;
  }
  .contact-icon {
    width: 14px; height: 14px; background: var(--text-light); border-radius: 2px;
    display: flex; align-items: center; justify-content: center;
  }
  .contact-icon svg { width: 10px; height: 10px; }

  .back-stripe {
    position: absolute; left: 58px; top: 0; width: 40px; height: 100%;
    background: linear-gradient(90deg, var(--silver) 0%, var(--silver-light) 50%, var(--silver) 100%);
  }
  .back-url {
    position: absolute; left: 78px; top: 155px;
    transform: translate(-50%, -50%) rotate(90deg);
    font-size: 13px; color: var(--ink); letter-spacing: 0.3px; white-space: nowrap;
  }
</style>
</head>
<body>
<main class="canvas">

  <section class="card card-front" aria-label="Card front">
    <svg class="card-shape" viewBox="0 0 540 310" preserveAspectRatio="none" aria-hidden="true">
      <path d="M300 0 C 250 110, 300 220, 255 310 L 540 310 L 540 0 Z" fill="#bdbdbd"/>
      <path d="M316 0 C 266 110, 316 220, 271 310 L 540 310 L 540 0 Z" fill="#2b2b2b"/>
    </svg>
    <span class="brand-name">LUMA</span>
    <div class="identity">
      <p class="identity-name">EMPLOYEE NAME</p>
      <p class="identity-role">Development Manager</p>
    </div>
    <ul class="contact-list">
      <li class="contact-item">
        <span class="contact-icon"><svg viewBox="0 0 10 10"><rect x="2.5" y="0.5" width="5" height="9" rx="1" fill="#2b2b2b"/></svg></span>
        (318) 4207265518
      </li>
      <li class="contact-item">
        <span class="contact-icon"><svg viewBox="0 0 10 10"><rect x="0.5" y="2" width="9" height="6" fill="#2b2b2b"/><path d="M0.5 2 L5 5.5 L9.5 2" stroke="#f2f2f2" stroke-width="0.8" fill="none"/></svg></span>
        hello@lumadrift.com
      </li>
      <li class="contact-item">
        <span class="contact-icon"><svg viewBox="0 0 10 10"><circle cx="5" cy="5" r="4.2" fill="none" stroke="#2b2b2b" stroke-width="1"/><path d="M0.8 5 H9.2 M5 0.8 V9.2" stroke="#2b2b2b" stroke-width="0.8"/><ellipse cx="5" cy="5" rx="2" ry="4.2" fill="none" stroke="#2b2b2b" stroke-width="0.8"/></svg></span>
        www.lumadrift.com
      </li>
    </ul>
  </section>

  <section class="card card-back" aria-label="Card back">
    <div class="back-stripe"></div>
    <span class="back-url">www.lumadrift.com</span>
    <span class="brand-name">LUMA</span>
  </section>

</main>
</body>
</html>
```